Creative UI design for web application

I need a new UI design for my web application. It will be used by small and micro business owners to plan & implement growth tactics.

I've attached the current design (which I'm open to be changed) - but in particular I need to design the centre of the screen, where the work actually happens.

There needs to be place for a title (YOUR BUSINESS) and description (say 1-2 paragraphs of text) - and am happy to include icons or imagery where makes sense. It may make sense for the user to be able to upload their business logo and name, for example.

This screen will be used by the business owner to understand the real value they offer potential customers and their point of difference - why they exist and why potential customers should care.

They'll use the information they put into this screen to plan things like their messaging.

Following that, there needs to be 2 sections in the dashboard.

The first section is titled "WHO YOU ARE"

The first section will include a number of boxes that the user can input information into, as follows:

- Logo
- Business name
- Business tag line
- Business vision
- Business bio
- Brand colours (these should end up as swatches based on the colour code they enter) - the colour code for each colour swatch should also be visible.
- Key competitors
- SWOT analysis (boxes to enter their strengths, weaknesses, opportunities and threats).

The second section is titled "WHY YOU EXIST"

The second section will include a number of boxes that the user can input information (text) into, as follows:

- Who are your ideal customers?
- What problem are you trying to solve for them?
- What pain points will this remove for them?
- How do you solve it?
- How else could this problem be solved?
- Who offers these other solutions?
- Why is your solution better?
- How much does your solution cost?
- What value are you providing to justify this cost?
- How will this make their life/job easier/better?

They should be able to write a decent amount of information in the boxes.

There should ideally be a place for a description for each of these text fields (for both section 1 & 2) as well so I can give them a little bit more direction around what to put in the box. Alternatively there could be a little icon (say a question mark or "i") that they could click on to view instructions. The instructions will be around 2-4 sentences long for each text field.

You have 2 options:

a) This all needs to appear on the one screen, and the navigation needs to be visible (as per the example attached but feel free to recreate this navigation)

Note: the page can scroll below the fold - but please provide the design for the full length of the page.

b) Potentially the 2 sections could actually be in 2 different items in the menu - YOUR BUSINESS and YOUR VALUE (which would sit next to YOUR BUSINESS and before YOUR CUSTOMER in the screenshot provided). feel free to design them as 2 separate screens if you prefer.

I have attached a screenshot of the app as it stands today (screen shot 2017) which would still exist in the new design but under a different section (the learn section from the plan2 mockup attached)

I have mocked up how this new screen could look if broken into 2 and that's also attached. If you can make this come to life - and look more engaging that would be helpful! :)

Target Market(s)

Small and micro business owners

Industry/Entity Type

Marketing

Number of Pages Required

1 page

Font styles to use
Sans Serif
Other font styles liked:
• Montserrat

Colors
87cfc6
d2a4cc
ffffff
85cae6
e8e8e8
5c5c5c

Requirements
Must have
• Use of my brand colours: #cc8eb2, #76d6c8, #68c7ff as well as white and #595959. Must be visually pleasing / engaging, designed for desktop (as it's a desktop application), really easy to use / navigate.
• Use font Montserrat light & Montserrat Regular or Bold. Mostly should be Montserrat light.
Nice to have
• Would be nice to see how this would look on mobile (as the application is responsive) but this is not mandatory.
Should not have
• Should not look too corporate or dry.

```html
<!DOCTYPE html>
<html lang="en">
<head>
<meta charset="utf-8">
<title>RiseLeaf – Your Business</title>
<link rel="stylesheet" href="https://fonts.googleapis.com/css2?family=Montserrat:wght@300;400;500;600&display=swap">
<style>
:root{
  --bar:#333333;
  --pink:#d4a6cf;
  --pink-btn:#d6a9d0;
  --blue:#85cae6;
  --page:#f5f5f5;
  --card:#ffffff;
  --line:#dcdcdc;
  --text:#5c5c5c;
  --muted:#777777;
  --footer:#5a5a5a;
  --s1:#3b5998;--s2:#1da1f2;--s3:#dd2c2c;--s4:#1f5f8b;
}
*{box-sizing:border-box;margin:0;padding:0}
html,body{width:1200px;height:3422px;overflow:hidden}
body{font-family:"Montserrat",sans-serif;font-weight:300;color:var(--text);background:var(--page)}

.topbar{height:62px;background:var(--bar);position:relative;color:#fff}
.brand{position:absolute;left:105px;top:20px;font-size:19px;font-weight:500;letter-spacing:.5px}
.main-nav{position:absolute;left:365px;top:22px;display:flex;gap:32px;font-size:15px;font-weight:400}
.main-nav .active{color:#d9a3d1}
.user-nav{position:absolute;right:160px;top:22px;display:flex;gap:30px;font-size:15px;font-weight:400}
.user-nav span{display:flex;align-items:center;gap:8px}

.tabbar{height:41px;background:#fff;position:relative;border-bottom:1px solid #eee}
.tabs{position:absolute;left:98px;top:0;display:flex;height:41px;font-size:15px;font-weight:400;color:#444}
.tabs a{display:flex;align-items:center;padding:0 16px;text-decoration:none;color:inherit}
.tabs a.active{background:var(--pink);color:#fff;padding:0 15px}
.social{position:absolute;left:905px;top:0;display:flex}
.social i{width:49px;height:41px;display:block}

.hero{height:463px;background:var(--pink);position:relative;overflow:hidden;color:#fff}
.hero-photo{position:absolute;right:0;top:0;width:660px;height:463px;
  background:linear-gradient(120deg,#c9b7a6 0%,#e9d7c2 35%,#f3e6d6 60%,#bfa890 100%);
  clip-path:polygon(23% 0,100% 0,100% 100%,0 100%)}
.hero-badge{position:absolute;left:100px;top:176px;width:122px;height:122px;border-radius:50%;background:#111;border:3px solid #fff;
  display:flex;align-items:center;justify-content:center;text-align:center;font-size:14px;font-weight:400;color:#fff;line-height:1.3}
.hero-name{position:absolute;left:246px;top:186px;font-size:23px;font-weight:400;letter-spacing:1px}
.hero-contact{position:absolute;left:246px;top:228px;font-size:14px;line-height:29px}
.hero-contact div{display:flex;align-items:center;gap:8px}
.hero-text{position:absolute;left:100px;top:333px;width:460px;font-size:12.5px;line-height:24px}

.section{width:1004px;margin:0 auto}
.section-title{text-align:center;font-size:24px;font-weight:500;color:#222;letter-spacing:1px;height:36px;line-height:36px}
.who{padding-top:92px}
.who .section-title{margin-bottom:20px}
.grid{display:grid;column-gap:30px}
.g2{grid-template-columns:1fr 1fr}
.g3{grid-template-columns:1fr 1fr 1fr}
.card{background:var(--card);border:1px solid var(--line)}
.card-head{background:var(--blue);color:#fff;font-size:15px;font-weight:400;padding:0 22px;height:42px;display:flex;align-items:center;justify-content:space-between;letter-spacing:.5px}
.card-head.q{height:56px;line-height:19px;letter-spacing:0}
.card-head.q span{max-width:78%}
.card-body{padding:20px 22px;font-size:12.5px;line-height:22px}
.row{margin-bottom:40px}
.h270 .card{height:270px}
.h274 .card{height:274px}

.file-input{margin-top:14px;height:42px;border:1px solid #ccc;width:100%}
.file-row{margin-top:20px;display:flex;align-items:center;gap:18px;font-size:11.5px;font-weight:400}
.btn{background:var(--pink-btn);color:#fff;border-radius:20px;width:110px;height:39px;display:flex;align-items:center;justify-content:center;font-size:11.5px;font-weight:400}

.swatches{display:grid;grid-template-columns:repeat(8,50px);gap:7px;padding:22px 24px}
.swatches i{height:50px;display:block}

.swot .card{height:169px}
.swot-cols{display:grid;grid-template-columns:repeat(4,1fr);gap:14px;padding:22px 22px}
.swot-cols label{font-size:13px;font-weight:400;display:block;margin-bottom:7px}
.swot-cols div div{height:41px;border:1px solid #ccc}

.divider{width:1004px;margin:78px auto 0;border-top:2px solid #ddd}
.why{padding-top:58px}
.why .section-title{margin-bottom:28px}
.why .row{margin-bottom:39px}
.why .card{height:272px}

.footer{position:absolute;left:0;top:3353px;width:1200px;height:69px;background:var(--footer);color:#fff;font-size:12px;font-weight:400;display:flex;align-items:center;justify-content:center}
</style>
</head>
<body>
<header class="topbar">
  <div class="brand">RiseLeaf</div>
  <nav class="main-nav"><span class="active">Plan</span><span>Learn</span><span>Remember</span></nav>
  <nav class="user-nav">
    <span><svg width="14" height="14" viewBox="0 0 14 14"><circle cx="7" cy="4" r="3.3" fill="#fff"/><path d="M0.5 14a6.5 5.5 0 0 1 13 0z" fill="#fff"/></svg>My Profile</span>
    <span><svg width="14" height="14" viewBox="0 0 14 14" fill="none" stroke="#fff" stroke-width="1.8"><path d="M5 2H2v10h3M6 7h7M10 4l3 3-3 3"/></svg>Log Out</span>
  </nav>
</header>

<div class="tabbar">
  <nav class="tabs">
    <a class="active">Your Business</a><a>Your Products</a><a>Your Customers</a><a>Your Goals</a><a>Your Plan</a>
  </nav>
  <div class="social"><i style="background:var(--s1)"></i><i style="background:var(--s2)"></i><i style="background:var(--s3)"></i><i style="background:var(--s4)"></i></div>
</div>

<section class="hero">
  <div class="hero-photo" role="img" aria-label="Photo of a makeup artist applying makeup with a brush"></div>
  <div class="hero-badge">Nora Bell</div>
  <h1 class="hero-name">NORA BELL MAKEUP</h1>
  <div class="hero-contact">
    <div><svg width="13" height="13" viewBox="0 0 13 13"><circle cx="6.5" cy="6.5" r="6" fill="#fff"/></svg>norabellmakeup.com</div>
    <div><svg width="13" height="11" viewBox="0 0 13 11"><rect width="13" height="11" rx="1" fill="#fff"/><path d="M1 1.5l5.5 4 5.5-4" stroke="#d4a6cf" fill="none"/></svg>hello@norabellmakeup.com</div>
  </div>
  <p class="hero-text">At vero eos et accusamus et iusto odio dignissimos ducimus qui blanditiis praesentium voluptatum deleniti atque corrupti quos dolores et quas molestias excepturi sint occaecati cupiditate non provident, similique sunt in culpa qui officia deserunt mollitia animi, id est laborum et dolorum fuga harum quidem rerum facilis est et expedita distinctio. Nam libero tempore, cum soluta nobis est.</p>
</section>

<section class="section who">
  <h2 class="section-title">WHO YOU ARE</h2>
  <div class="grid g2 row h270">
    <div class="card"><div class="card-head">LOGO</div>
      <div class="card-body"><div class="file-input"></div>
        <div class="file-row"><span class="btn">BROWSE</span><span>No File Selected</span></div></div></div>
    <div class="card"><div class="card-head">BUSINESS NAME</div>
      <div class="card-body">Nam libero tempore, cum soluta nobis est eligendi opticumque nihil impedit quo minus id quod maxime placeat facere posmus, omnis voluptas assumenda est, omnis dolor re..</div></div>
  </div>
  <div class="grid g3 row h270">
    <div class="card"><div class="card-head">BUSINESS TAG LINE</div><div class="card-body">Nam libero tempore, cum soluta nobiest eligendi opticumque nihil impedit qumi nus id quod maxime place.</div></div>
    <div class="card"><div class="card-head">BUSINESS VISION</div><div class="card-body">Nam libero tempore, cum soluta nobiest eligendi opticumque nihil impedit qumi nus id quod maxime place.</div></div>
    <div class="card"><div class="card-head">BUSINESS BIO</div><div class="card-body">Nam libero tempore, cum soluta nobiest eligendi opticumque nihil impedit qumi nus id quod maxime place.</div></div>
  </div>
  <div class="grid g2 row h274" style="margin-bottom:36px">
    <div class="card"><div class="card-head">BRAND COLOURS</div>
      <div class="swatches">
        <i style="background:#464a55"></i><i style="background:#8a4a24"></i><i style="background:#c9b27a"></i><i style="background:#8a6a45"></i><i style="background:#c65a72"></i><i style="background:#b872a4"></i><i style="background:#4c5a8a"></i><i style="background:#8aae4a"></i>
        <i style="background:#4a4a56"></i><i style="background:#7a8a2a"></i><i style="background:#9cc97a"></i><i style="background:#7a9a4a"></i><i style="background:#d4a064"></i><i style="background:#b86a64"></i><i style="background:#6a4a8a"></i><i style="background:#4ab064"></i>
        <i style="background:#3f4a4a"></i><i style="background:#8a2a6a"></i><i style="background:#d478a0"></i><i style="background:#8a4a74"></i><i style="background:#a85ad4"></i><i style="background:#7a6ab8"></i><i style="background:#4a8a74"></i><i style="background:#b8644a"></i>
      </div></div>
    <div class="card"><div class="card-head">KEY COMPETITORS</div>
      <div class="card-body">Nam libero tempore, cum soluta nobis est eligendi opticumque nihil impedit quo minus id quod maxime placeat facere posmus, omnis voluptas assumenda est, omnis dolor re..</div></div>
  </div>
  <div class="swot">
    <div class="card"><div class="card-head">SWOT ANALYSIS</div>
      <div class="swot-cols">
        <div><label>Strengths</label><div></div></div>
        <div><label>Weaknesses</label><div></div></div>
        <div><label>Opportunities</label><div></div></div>
        <div><label>Threats</label><div></div></div>
      </div></div>
  </div>
</section>

<div class="divider"></div>

<section class="section why">
  <h2 class="section-title">WHY YOU EXIST</h2>
  <div class="grid g2 row">
    <div class="card"><div class="card-head q"><span>Who are your ideal customers?</span><svg class="info" width="20" height="20" viewBox="0 0 20 20"><circle cx="10" cy="10" r="9" fill="#fff"/><rect x="9" y="8.5" width="2" height="6.5" fill="#85cae6"/><circle cx="10" cy="6" r="1.2" fill="#85cae6"/></svg></div>
      <div class="card-body">Nam libero tempore, cum soluta nobis est eligendi opticumque nihil impedit quo minus id quod maxime placeat facere posmus, omnis voluptas assumenda est, omnis dolor re..</div></div>
    <div class="card"><div class="card-head q"><span>What problem are you trying to solve for them?</span><svg width="20" height="20" viewBox="0 0 20 20"><circle cx="10" cy="10" r="9" fill="#fff"/><rect x="9" y="8.5" width="2" height="6.5" fill="#85cae6"/><circle cx="10" cy="6" r="1.2" fill="#85cae6"/></svg></div>
      <div class="card-body">Nam libero tempore, cum soluta nobis est eligendi opticumque nihil impedit quo minus id quod maxime placeat facere posmus, omnis voluptas assumenda est, omnis dolor re..</div></div>
  </div>
  <div class="grid g3 row">
    <div class="card"><div class="card-head q"><span>How do you solve it?</span><svg width="20" height="20" viewBox="0 0 20 20"><circle cx="10" cy="10" r="9" fill="#fff"/><rect x="9" y="8.5" width="2" height="6.5" fill="#85cae6"/><circle cx="10" cy="6" r="1.2" fill="#85cae6"/></svg></div>
      <div class="card-body">Nam libero tempore, cum soluta nobiest eligendi opticumque nihil impedit qumi nus id quod maxime place.</div></div>
    <div class="card"><div class="card-head q"><span>Who offers these other solutions?</span><svg width="20" height="20" viewBox="0 0 20 20"><circle cx="10" cy="10" r="9" fill="#fff"/><rect x="9" y="8.5" width="2" height="6.5" fill="#85cae6"/><circle cx="10" cy="6" r="1.2" fill="#85cae6"/></svg></div>
      <div class="card-body">Nam libero tempore, cum soluta nobiest eligendi opticumque nihil impedit qumi nus id quod maxime place.</div></div>
    <div class="card"><div class="card-head q"><span>Why is your solution better?</span><svg width="20" height="20" viewBox="0 0 20 20"><circle cx="10" cy="10" r="9" fill="#fff"/><rect x="9" y="8.5" width="2" height="6.5" fill="#85cae6"/><circle cx="10" cy="6" r="1.2" fill="#85cae6"/></svg></div>
      <div class="card-body">Nam libero tempore, cum soluta nobiest eligendi opticumque nihil impedit qumi nus id quod maxime place.</div></div>
  </div>
  <div class="grid g2 row">
    <div class="card"><div class="card-head q"><span>What pain points will this remove for them?</span><svg width="20" height="20" viewBox="0 0 20 20"><circle cx="10" cy="10" r="9" fill="#fff"/><rect x="9" y="8.5" width="2" height="6.5" fill="#85cae6"/><circle cx="10" cy="6" r="1.2" fill="#85cae6"/></svg></div>
      <div class="card-body">Nam libero tempore, cum soluta nobis est eligendi opticumque nihil impedit quo minus id quod maxime placeat facere posmus, omnis voluptas assumenda est, omnis dolor re..</div></div>
    <div class="card"><div class="card-head q"><span>What value are you providing to justify this cost?</span><svg width="20" height="20" viewBox="0 0 20 20"><circle cx="10" cy="10" r="9" fill="#fff"/><rect x="9" y="8.5" width="2" height="6.5" fill="#85cae6"/><circle cx="10" cy="6" r="1.2" fill="#85cae6"/></svg></div>
      <div class="card-body">Nam libero tempore, cum soluta nobis est eligendi opticumque nihil impedit quo minus id quod maxime placeat facere posmus, omnis voluptas assumenda est, omnis dolor re..</div></div>
  </div>
  <div class="grid g3 row">
    <div class="card"><div class="card-head q"><span>How much does your solution cost?</span><svg width="20" height="20" viewBox="0 0 20 20"><circle cx="10" cy="10" r="9" fill="#fff"/><rect x="9" y="8.5" width="2" height="6.5" fill="#85cae6"/><circle cx="10" cy="6" r="1.2" fill="#85cae6"/></svg></div>
      <div class="card-body">Nam libero tempore, cum soluta nobiest eligendi opticumque nihil impedit qumi nus id quod maxime place.</div></div>
    <div class="card"><div class="card-head q"><span>How will this make their life/job easier/better?</span><svg width="20" height="20" viewBox="0 0 20 20"><circle cx="10" cy="10" r="9" fill="#fff"/><rect x="9" y="8.5" width="2" height="6.5" fill="#85cae6"/><circle cx="10" cy="6" r="1.2" fill="#85cae6"/></svg></div>
      <div class="card-body">Nam libero tempore, cum soluta nobiest eligendi opticumque nihil impedit qumi nus id quod maxime place.</div></div>
    <div class="card"><div class="card-head q"><span>How else could this problem be solved?</span><svg width="20" height="20" viewBox="0 0 20 20"><circle cx="10" cy="10" r="9" fill="#fff"/><rect x="9" y="8.5" width="2" height="6.5" fill="#85cae6"/><circle cx="10" cy="6" r="1.2" fill="#85cae6"/></svg></div>
      <div class="card-body">Nam libero tempore, cum soluta nobiest eligendi opticumque nihil impedit qumi nus id quod maxime place.</div></div>
  </div>
</section>

<footer class="footer">Copyright © 2017, RiseLeaf. All rights reserved.</footer>
</body>
</html>
```